Business Card Design Project

We are a construction company in Orange County, CA. We need a two sided business card. We would like the back to be our logo with web URL. Front should included Name, title, address, phone, fax and email address.

our address is
627 West Dorrance Blvd, Suite 308
Brea, CA 92718

Our logo files are attached.

Construction

```html
<!DOCTYPE html>
<html lang="en">
<head>
<meta charset="utf-8">
<title>Strata Business Card</title>
<link href="https://fonts.googleapis.com/css2?family=Source+Sans+3:wght@400;600;800&display=swap" rel="stylesheet">
<style>
  :root {
    --brand-blue: #1b4f82;
    --ink-black: #0b0b0b;
    --text-gray: #444444;
    --card-white: #ffffff;
    --backdrop: #ece8e3;
  }
  * { margin: 0; padding: 0; box-sizing: border-box; }
  html, body { width: 1200px; height: 415px; overflow: hidden; }
  body {
    background: var(--backdrop);
    font-family: "Source Sans 3", "Segoe UI", sans-serif;
    position: relative;
  }
  .card {
    position: absolute;
    width: 525px;
    height: 300px;
    background: var(--card-white);
    box-shadow: 0 2px 5px rgba(0,0,0,0.25);
    overflow: hidden;
  }
  .card--front { left: 55px; top: 55px; }
  .card--back { left: 625px; top: 60px; }

  .accent { position: absolute; }
  .accent--top-band { left: 208px; top: 0; width: 317px; height: 13px; background: var(--brand-blue); }
  .accent--top-tab { left: 470px; top: 13px; width: 55px; height: 10px; background: var(--ink-black); }
  .accent--side-blue { left: 0; top: 210px; width: 12px; height: 75px; background: var(--brand-blue); }
  .accent--side-black { left: 12px; top: 229px; width: 12px; height: 71px; background: var(--ink-black); }
  .accent--base-black { left: 0; top: 285px; width: 24px; height: 15px; background: var(--ink-black); }

  .brand-name {
    position: absolute;
    width: 300px;
    text-align: center;
    color: var(--brand-blue);
    font-weight: 800;
    font-size: 90px;
    line-height: 1;
    letter-spacing: -1px;
  }
  .card--front .brand-name { left: 170px; top: 12px; }
  .card--back .brand-name { left: 112px; top: 86px; }

  .holder { position: absolute; left: 37px; top: 238px; color: var(--brand-blue); }
  .holder__name { font-weight: 600; font-size: 19px; line-height: 24px; }
  .holder__title { font-size: 17px; line-height: 22px; }

  .contact-list {
    position: absolute; right: 63px; top: 167px;
    list-style: none; text-align: right;
    color: var(--text-gray); font-size: 13.5px; line-height: 17px;
  }
  .contact-list li { display: flex; justify-content: flex-end; align-items: center; gap: 5px; }
  .contact-list svg { width: 11px; height: 11px; fill: var(--text-gray); }

  .address {
    position: absolute; right: 63px; top: 246px;
    text-align: right; font-style: normal;
    color: var(--text-gray); font-size: 13.5px; line-height: 17px;
  }

  .web-address {
    position: absolute; left: 0; top: 192px; width: 100%;
    text-align: center; color: var(--text-gray);
    font-size: 15px; letter-spacing: 2.4px;
  }
</style>
</head>
<body>
  <section class="card card--front" aria-label="Card front">
    <div class="accent accent--top-band"></div>
    <div class="accent accent--top-tab"></div>
    <div class="accent accent--side-blue"></div>
    <div class="accent accent--side-black"></div>
    <div class="accent accent--base-black"></div>

    <div class="brand-name">STRATA</div>

    <ul class="contact-list">
      <li><svg viewBox="0 0 12 12" aria-hidden="true"><path d="M3 1l2 2.5-1.2 1.3a7 7 0 0 0 3.4 3.4L8.5 7 11 9l-1.3 2C5.5 11 1 6.5 1 2.3z"/></svg>01-555-0142</li>
      <li><svg viewBox="0 0 12 12" aria-hidden="true"><path d="M3 1h6v3H3zM1 5h10v5H9v-2H3v2H1zM3.5 9h5v2h-5z"/></svg>01-555-0143</li>
      <li><svg viewBox="0 0 12 12" aria-hidden="true"><path d="M1 3h10v7H1zM1.5 3.5L6 7l4.5-3.5" stroke="#fff" stroke-width="0.9"/></svg>info@stratabuild.com</li>
      <li><svg viewBox="0 0 12 12" aria-hidden="true"><circle cx="6" cy="6" r="5"/><path d="M1 6h10M6 1c-2.5 3-2.5 7 0 10M6 1c2.5 3 2.5 7 0 10" stroke="#fff" stroke-width="0.8" fill="none"/></svg>www.stratabuild.com</li>
    </ul>

    <div class="holder">
      <div class="holder__name">Your Name</div>
      <div class="holder__title">Title</div>
    </div>

    <address class="address">
      627 West Dorrance Blvd<br>
      Suite 308, Brea, CA&nbsp;&nbsp;92718
    </address>
  </section>

  <section class="card card--back" aria-label="Card back">
    <div class="brand-name">STRATA</div>
    <div class="web-address">www.stratabuild.com</div>
  </section>
</body>
</html>
```